Morlavik APP redesign and color change

I am looking for a new design for my app. Please see the attached current design.

Currently, I have a functioning app but the colors and design are awful!
The logo is great but the rest of the app needs a refresh.
(Logo hi res not yet available but will upload soon.)
New colors or anything that is cutting edge.

Basically: It is a secure social media app within a school system where the teachers, students and parents can text, exchange photos, plan curriculum, etc.

I NEED ONLY landing page with a new look!
Looking for one distinct design for the landing page with new look.
The developer will apply this one design towards the rest of the pages/app screens.

Because part of the social media I need the feel and look of what is now the trend. Something that will attract and keep the client(s) interested. I am really leaving all the creative work to the designer and open to any suggestions.

Target Market(s)

Schools, community, teachers, students, colleges, sport teams

Industry/Entity Type

Non Profit

Font styles to use
Serif
Sans Serif

Colors

Designer to choose colors to be used in the design.

Requirements
Must have
• Sharp, trendy, millennial feel
Nice to have
• Up to designer
Should not have
• Up to designer

```html
<!DOCTYPE html>
<html lang="en">
<head>
<meta charset="utf-8">
<title>Morlavik – Join Today</title>
<link rel="stylesheet" href="https://fonts.googleapis.com/css2?family=Poppins:wght@400;500;600;700&display=swap">
<style>
  :root {
    --page-bg: #f2eff0;
    --screen-bg: #ffffff;
    --navy: #1f2a6b;
    --navy-soft: #3a4584;
    --teal-a: #2ee6d6;
    --teal-b: #3a8fd0;
    --pink-a: #ff5fa8;
    --pink-b: #f0387a;
    --orange-a: #f2a52a;
    --orange-b: #ef7a2c;
    --violet-a: #c24fd0;
    --violet-b: #7a3ad8;
    --login-a: #ff5aa5;
    --login-b: #e8205a;
    --signup-a: #0ff0d8;
    --signup-b: #2f55c8;
    --badge-a: #c44b8e;
    --badge-b: #5a4fa8;
  }
  * { box-sizing: border-box; margin: 0; padding: 0; }
  html, body {
    width: 1200px;
    height: 900px;
    overflow: hidden;
    background: var(--page-bg);
    font-family: "Poppins", sans-serif;
  }
  .canvas {
    position: relative;
    width: 1200px;
    height: 900px;
  }
  .landing-screen {
    position: absolute;
    left: 365px;
    top: 30px;
    width: 470px;
    height: 840px;
    background: var(--screen-bg);
    overflow: hidden;
    box-shadow: 0 12px 40px rgba(40, 30, 60, 0.12);
  }
  .hero-grid {
    position: relative;
    display: grid;
    grid-template-columns: 1fr 1fr;
    grid-template-rows: 1fr 1fr;
    width: 100%;
    height: 500px;
  }
  .hero-tile { width: 100%; height: 100%; }
  .hero-tile--teal { background: linear-gradient(160deg, var(--teal-a), var(--teal-b)); }
  .hero-tile--pink { background: linear-gradient(160deg, var(--pink-a), var(--pink-b)); }
  .hero-tile--orange { background: linear-gradient(160deg, var(--orange-a), var(--orange-b)); }
  .hero-tile--violet { background: linear-gradient(160deg, var(--violet-a), var(--violet-b)); }
  .brand-badge {
    position: absolute;
    left: 50%;
    top: 50%;
    width: 112px;
    height: 112px;
    transform: translate(-50%, -50%);
    border-radius: 50%;
    background: #f4f1f3;
    padding: 10px;
    box-shadow: 0 4px 14px rgba(30, 20, 60, 0.25);
  }
  .brand-badge__core {
    width: 100%;
    height: 100%;
    border-radius: 50%;
    background: linear-gradient(160deg, var(--badge-a), var(--badge-b));
    display: flex;
    align-items: center;
    justify-content: center;
  }
  .brand-badge__name {
    color: #ffffff;
    font-weight: 600;
    font-size: 13px;
    letter-spacing: 0.2px;
  }
  .join-panel {
    text-align: center;
    padding-top: 52px;
  }
  .join-panel__title {
    color: var(--navy);
    font-weight: 600;
    font-size: 32px;
    line-height: 1.2;
  }
  .join-panel__lead {
    margin-top: 10px;
    color: var(--navy-soft);
    font-weight: 500;
    font-size: 16px;
    line-height: 1.5;
  }
  .join-actions {
    display: flex;
    justify-content: center;
    gap: 34px;
    margin-top: 44px;
  }
  .action-button {
    display: inline-flex;
    align-items: center;
    justify-content: center;
    width: 170px;
    height: 58px;
    border-radius: 29px;
    color: #ffffff;
    font-weight: 500;
    font-size: 20px;
    text-decoration: none;
    box-shadow: 0 8px 18px rgba(40, 30, 80, 0.18);
  }
  .action-button--login { background: linear-gradient(135deg, var(--login-a), var(--login-b)); }
  .action-button--signup { background: linear-gradient(135deg, var(--signup-a), var(--signup-b)); }
</style>
</head>
<body>
<main class="canvas">
  <section class="landing-screen">
    <div class="hero-grid">
      <div class="hero-tile hero-tile--teal" role="img" aria-label="Photo of students working together on a tablet, tinted teal"></div>
      <div class="hero-tile hero-tile--pink" role="img" aria-label="Photo of a student smiling at a phone, tinted pink"></div>
      <div class="hero-tile hero-tile--orange" role="img" aria-label="Photo of a student with glasses studying with books, tinted orange"></div>
      <div class="hero-tile hero-tile--violet" role="img" aria-label="Photo of friends sharing a phone, tinted violet"></div>
      <div class="brand-badge">
        <div class="brand-badge__core"><span class="brand-badge__name">Morlavik</span></div>
      </div>
    </div>
    <div class="join-panel">
      <h1 class="join-panel__title">Join Today</h1>
      <p class="join-panel__lead">Interact with your Teachers<br>students and Parents in better way</p>
      <div class="join-actions">
        <a class="action-button action-button--login" href="#">Login</a>
        <a class="action-button action-button--signup" href="#">Sign up</a>
      </div>
    </div>
  </section>
</main>
</body>
</html>
```